Looking to Redesign Brevonix.com website

You guys did one of the brochures for brevonix.com and I would like to see if we can go ahead and get an estimate for a redesigned web site for the company. We currently have a couple of pages on brevonix.com which are very much a starter type site.

The new design will need to reflect some of the things discussed in the brochure. It will have flash. Needs to be designed for simple hosting using cpanels.

The site needs to have between 12 and 15 pages with flash pages to move through features. Integrated with twitter like it is now, and contact forms delivered from our CRM along with other interactive features such as subscription to newsletter, etc...

I don't have lots of details on how to proceed yet, but here are some competitor sites:

Can we take a look at potential costs involved in the redo of the site as vague as my description above can permit.

Target Market(s)

Business to Business

Number of Pages Required

5+ page

Font styles to use
Sans Serif

Requirements
Must have
• Must have professional feel. Similar to brochure. and logo.
• Include our story in the discussion.
• embedded links to our CRM for popup contact forms.
• Logo files and 2 types of brochures uploaded.
• Important to keep color scheme
Nice to have
• Flash and some movement
Should not have
• Not sure yet

```html
<!DOCTYPE html>
<html lang="en">
<head>
<meta charset="utf-8">
<title>Brevonix Universal Communication</title>
<link rel="stylesheet" href="https://fonts.googleapis.com/css2?family=Open+Sans:ital,wght@0,400;0,600;1,400&display=swap">
<style>
:root{
  --red:#c8000a;
  --red-bright:#d80b0f;
  --red-deep:#b00008;
  --ink:#333333;
  --body:#555555;
  --white:#ffffff;
  --quote-bg:#e6e6e6;
  --footer:#333333;
  --footer-bottom:#2a2a2a;
  --footer-text:#dddddd;
  --input:#5a5a5a;
}
*{box-sizing:border-box;margin:0;padding:0}
html,body{width:1200px;height:2256px;overflow:hidden}
body{position:relative;font-family:"Open Sans",Arial,sans-serif;color:var(--body);background:var(--white)}
.abs{position:absolute}

/* header */
.top-rule{left:0;top:0;width:1200px;height:3px;background:var(--red)}
.brand{left:132px;top:44px;display:flex;align-items:center;gap:14px}
.brand-dot{width:64px;height:64px;border-radius:50%;background:var(--red)}
.brand-name{font-size:34px;font-weight:600;color:var(--red);letter-spacing:1px}
.contact-bar{top:42px;right:168px;display:flex;align-items:center;gap:16px;font-size:12px;color:var(--ink)}
.contact-bar .item{display:flex;align-items:center;gap:12px}
.icon-badge{width:22px;height:22px;border-radius:50%;background:var(--red);display:flex;align-items:center;justify-content:center}
.search{left:1049px;top:48px}
.nav{top:101px;left:390px;font-size:12px;color:var(--ink);text-transform:uppercase}
.nav a{position:absolute;white-space:nowrap;color:inherit;text-decoration:none}
.nav a.active{color:var(--red)}

/* hero */
.hero{left:0;top:158px;width:1200px;height:447px;background:radial-gradient(ellipse at 50% 40%,#4a4a4a 0%,#262626 55%,#0d0d0d 100%)}
.hero-title{top:292px;left:0;width:1200px;text-align:center;color:var(--white);font-size:35px;font-weight:400;letter-spacing:.5px}
.hero-sub{top:356px;left:0;width:1200px;text-align:center;color:var(--white);font-size:12px}
.btn{display:flex;align-items:center;justify-content:center;background:var(--red);color:var(--white);font-size:12px;text-transform:uppercase;border-radius:3px}
.hero-btn{left:540px;top:403px;width:119px;height:47px}
.dots{top:543px;left:570px;display:flex;gap:19px}
.dots span{width:8px;height:8px;border-radius:50%;background:#bbbbbb}
.dots span.on{background:var(--red)}

/* about */
.h2{font-size:26px;font-weight:400;color:var(--red);text-transform:uppercase}
.about-h{left:132px;top:650px}
.copy{font-size:12px;line-height:19.5px;color:var(--body)}
.about-copy{left:132px;top:698px;width:458px}
.copy p{margin-bottom:19.5px}
.about-diagram{left:630px;top:654px;width:435px;height:343px;border:1px solid #888;background:linear-gradient(90deg,#eeeeea 0%,#f3efe0 55%,#ececea 100%)}
.about-btn{left:132px;top:959px;width:110px;height:44px}

/* benefits */
.benefits{left:0;top:1093px;width:1200px;height:471px;background:linear-gradient(180deg,var(--red-bright) 0%,var(--red-deep) 100%)}
.benefits-h{top:1155px;left:0;width:1200px;text-align:center;color:var(--white);font-size:24px;font-weight:400}
.benefits-copy{top:1213px;left:130px;width:940px;text-align:center;color:#f1a5a5;font-size:11.5px;line-height:19px}
.benefit{width:200px;text-align:center}
.benefit .disc{width:90px;height:90px;border-radius:50%;background:var(--white);margin:0 auto;display:flex;align-items:center;justify-content:center}
.benefit .label{margin-top:28px;color:var(--white);font-size:20px;text-transform:uppercase;white-space:nowrap}

/* why + testimonial */
.why-h{left:134px;top:1616px}
.why-copy{left:132px;top:1663px;width:558px}
.why-btn{left:132px;top:1841px;width:110px;height:44px}
.test-h{left:734px;top:1616px}
.quote{left:737px;top:1668px;width:331px;height:212px;background:var(--quote-bg);padding:34px 28px 0 28px;font-size:11.5px;line-height:19px;color:var(--body);text-align:justify}
.quote .mark{position:absolute;left:26px;top:20px}
.quote .lead{text-indent:40px}
.quote cite{display:block;margin-top:34px;font-style:italic;font-size:12px;color:var(--ink)}

/* footer */
.footer{left:0;top:1940px;width:1200px;height:248px;background:var(--footer);border-top:4px solid var(--red)}
.footer-bottom{left:0;top:2188px;width:1200px;height:68px;background:var(--footer-bottom)}
.f-h{font-size:14px;color:var(--white);text-transform:uppercase;letter-spacing:.5px}
.f-links{font-size:11px;line-height:19.3px;color:var(--white);list-style:none}
.f-contact{font-size:11px;color:var(--white);list-style:none}
.f-contact li{display:flex;gap:12px;margin-bottom:11px;line-height:15px}
.f-contact svg{flex:none;margin-top:1px}
.f-news-sub{font-size:11px;color:var(--footer-text)}
.f-input{left:590px;top:2065px;width:195px;height:33px;background:var(--input);color:#eee;font-size:11px;padding:10px 10px}
.f-sub{left:590px;top:2112px;width:82px;height:26px;border-radius:2px;font-size:11px}
.f-mark{left:865px;top:2000px;display:flex;align-items:center;gap:14px}
.f-mark .dot{width:110px;height:110px;border-radius:50%;background:#444444}
.f-mark .name{font-size:30px;font-weight:600;color:#4a4a4a}
.copyright{left:132px;top:2215px;font-size:12px;color:var(--white)}
.social{top:2206px;left:914px;display:flex;gap:3px}
.social span{width:36px;height:36px;border-radius:50%;border:2px solid var(--white)}
</style>
</head>
<body>

<header>
  <div class="abs top-rule"></div>
  <div class="abs brand"><span class="brand-dot"></span><span class="brand-name">brevonix</span></div>

  <div class="abs contact-bar">
    <span class="item">
      <span class="icon-badge"><svg width="11" height="11" viewBox="0 0 24 24"><path fill="#fff" d="M6.6 10.8a15.1 15.1 0 0 0 6.6 6.6l2.2-2.2c.3-.3.7-.4 1-.2 1.1.4 2.3.6 3.6.6.6 0 1 .4 1 1V20c0 .6-.4 1-1 1A17 17 0 0 1 3 4c0-.6.4-1 1-1h3.5c.6 0 1 .4 1 1 0 1.3.2 2.5.6 3.6.1.3 0 .7-.2 1z"/></svg></span>
      1800 555 014
    </span>
    <span class="item" style="margin-left:16px">
      <span class="icon-badge"><svg width="11" height="9" viewBox="0 0 22 16"><rect x="1" y="1" width="20" height="14" fill="none" stroke="#fff" stroke-width="2"/><path d="M1 1l10 8 10-8" fill="none" stroke="#fff" stroke-width="2"/></svg></span>
      hello@brevonix.com
    </span>
  </div>
  <svg class="abs search" width="14" height="14" viewBox="0 0 14 14"><circle cx="5.5" cy="5.5" r="4.2" fill="none" stroke="#c8000a" stroke-width="2"/><path d="M8.6 8.6l4 4" stroke="#c8000a" stroke-width="2.4"/></svg>

  <nav class="abs nav">
    <a class="active" style="left:0;top:0">Home</a>
    <a style="left:78px;top:0">About</a>
    <a style="left:163px;top:0">Why Brevonix</a>
    <a style="left:312px;top:0">Features</a>
    <a style="left:415px;top:0">Advantages</a>
    <a style="left:535px;top:0">Best of Class Hardware</a>
  </nav>
</header>

<section>
  <div class="abs hero" role="img" aria-label="Dark photograph of hands reaching toward a network of connected people icons"></div>
  <h1 class="abs hero-title">BREVONIX UNIVERSAL COMMUNICATION</h1>
  <p class="abs hero-sub">Brevonix melds the fresh ideas of youth with the reliability of experience</p>
  <a class="abs btn hero-btn">Read More</a>
  <div class="abs dots"><span></span><span class="on"></span><span></span></div>
</section>

<section>
  <h2 class="abs h2 about-h">About</h2>
  <div class="abs copy about-copy">
    <p>Brevonix has been in the business of providing Hosted based PBX services since early 2003.&nbsp; This is before most of the business world had ever heard of such a service.</p>
    <p>Yes.&nbsp; You may have never heard of us or our services...&nbsp; Fact is we have been providing services to corporate clients as a part of an IT managed services group and were not marketing to other businesses.<br>So what is different now?</p>
    <p>We have acquired a traditional services provider and we got spun off into our own entity.&nbsp; Now we are able to bring to the general market these unique services.&nbsp;&nbsp;Your solution will be completely custom to you, redundant, secure, reliable, and above all simple to use, access, and modify.</p>
  </div>
  <div class="abs about-diagram" role="img" aria-label="Illustrated network diagram of client offices connected through the internet to unified communication servers and redundant telephony providers"></div>
  <a class="abs btn about-btn">Read More</a>
</section>

<section>
  <div class="abs benefits"></div>
  <h2 class="abs benefits-h">BENEFITS</h2>
  <p class="abs benefits-copy">Discovering your needs, creating solutions that truly work Quick ROI: Equipment is included in the service Secure: Encrypted lines Easy installation: Very little business interruption Expandable: One unit at a time Intuitive: Easy to learn and run Fail-over: Calls go through even if a supplier phone company has outages Customized: Expandable speed-dial options Safety: 911 notification to managers</p>

  <div class="abs benefit" style="left:77px;top:1327px">
    <div class="disc"><svg width="28" height="22" viewBox="0 0 28 22"><path d="M2 8a17 17 0 0 1 24 0M6 12a11 11 0 0 1 16 0M10 16a5 5 0 0 1 8 0" fill="none" stroke="#c8000a" stroke-width="3" stroke-linecap="round"/><circle cx="14" cy="19.5" r="2" fill="#c8000a"/></svg></div>
    <div class="label">Wireless</div>
  </div>
  <div class="abs benefit" style="left:229px;top:1327px">
    <div class="disc"><svg width="28" height="20" viewBox="0 0 28 20"><rect x="1.5" y="1.5" width="25" height="17" fill="none" stroke="#c8000a" stroke-width="2.5"/><path d="M1.5 2l12.5 10L26.5 2" fill="none" stroke="#c8000a" stroke-width="2.5"/></svg></div>
    <div class="label">Email</div>
  </div>
  <div class="abs benefit" style="left:420px;top:1327px">
    <div class="disc"><svg width="28" height="24" viewBox="0 0 28 24"><ellipse cx="14" cy="10" rx="12" ry="8.5" fill="none" stroke="#c8000a" stroke-width="2.5"/><path d="M6 16l-2 6 7-4" fill="none" stroke="#c8000a" stroke-width="2.5" stroke-linejoin="round"/></svg></div>
    <div class="label">Text Messaging</div>
  </div>
  <div class="abs benefit" style="left:617px;top:1327px">
    <div class="disc"><svg width="26" height="26" viewBox="0 0 26 26"><circle cx="13" cy="13" r="12" fill="#c8000a"/><path d="M6 8c3 0 4 2 6 2s1 4 3 4 2 4 0 6M18 4c-1 3 2 4 4 5" fill="none" stroke="#fff" stroke-width="2"/></svg></div>
    <div class="label">Web</div>
  </div>
  <div class="abs benefit" style="left:774px;top:1327px">
    <div class="disc"><svg width="26" height="28" viewBox="0 0 26 28"><rect x="7" y="1" width="13" height="8" fill="#c8000a"/><rect x="1" y="9" width="24" height="18" rx="2" fill="#c8000a"/><rect x="4" y="12" width="5" height="12" fill="#fff"/><g fill="#fff"><rect x="12" y="13" width="3" height="3"/><rect x="17" y="13" width="3" height="3"/><rect x="12" y="18" width="3" height="3"/><rect x="17" y="18" width="3" height="3"/></g></svg></div>
    <div class="label">Fax</div>
  </div>
  <div class="abs benefit" style="left:926px;top:1327px">
    <div class="disc"><svg width="18" height="30" viewBox="0 0 18 30"><rect x="1.5" y="1.5" width="15" height="27" rx="3" fill="none" stroke="#c8000a" stroke-width="2.5"/><circle cx="9" cy="24" r="1.6" fill="#c8000a"/></svg></div>
    <div class="label">Phone</div>
  </div>
</section>

<section>
  <h2 class="abs h2 why-h">Why Brevonix</h2>
  <div class="abs copy why-copy">
    <p>Honestly, your office phone system is probably the least sexy thing in your company – the minute the system is down,</p>
    <p>you're out of business – so you need a phone system that you can count on every minute of every day. But your phone system doesn't have to be boring, it can look great, too! With a sleek design and customized logos, these phones add a distinctive look sitting on the desk. What is even better, is how good this system makes you look to your customers. Whatever image you want to portray, Brevonix can help create it and still provide the flexible, reliable, quality service that you expect.</p>
  </div>
  <a class="abs btn why-btn">Read More</a>

  <h2 class="abs h2 test-h">Testimonial</h2>
  <blockquote class="abs quote">
    <svg class="mark" width="26" height="22" viewBox="0 0 26 22"><path d="M0 10C0 4 3 1 9 0v4C6 5 5 7 5 9h5v12H0zM14 10c0-6 3-9 9-10v4c-3 1-4 3-4 5h5v12H14z" fill="#8a8a8a"/></svg>
    <p class="lead">Nemo enim ipsam voluptatem quia voluptas sit aspernatur aut odit aut fugit, sed quia consequuntur magni dolores eos qui ratione voluptatem sequi nesciunt.Neque porro quisquam est, qui dolorem ipsum quia dolor sit amet, consectetur, adipisci velit</p>
    <cite>- Mara Quill -</cite>
  </blockquote>
</section>

<footer>
  <div class="abs footer"></div>

  <h3 class="abs f-h" style="left:132px;top:1988px">Quick Links</h3>
  <ul class="abs f-links" style="left:134px;top:2027px">
    <li>Home</li><li>About</li><li>Why brevonix</li><li>Features</li><li>Advantages</li><li>Best of Class Hardware</li>
  </ul>

  <h3 class="abs f-h" style="left:323px;top:1988px">Contact Us</h3>
  <ul class="abs f-contact" style="left:325px;top:2031px">
    <li><svg width="14" height="12" viewBox="0 0 14 12"><path d="M1 4c0-2 3-3 6-3s6 1 6 3v1h-3V4H4v1H1zM3 6h8l2 5H1z" fill="#fff"/></svg>1 555 010 4821</li>
    <li><svg width="14" height="13" viewBox="0 0 14 13"><rect x="3" y="0" width="8" height="4" fill="#fff"/><rect x="0" y="4" width="14" height="6" fill="#fff"/><rect x="3" y="8" width="8" height="5" fill="#fff" stroke="#333" stroke-width="1"/></svg>+44 20 7946 0321</li>
    <li><svg width="14" height="11" viewBox="0 0 14 11"><rect x=".8" y=".8" width="12.4" height="9.4" fill="none" stroke="#fff" stroke-width="1.4"/><path d="M1 1l6 5 6-5" fill="none" stroke="#fff" stroke-width="1.4"/></svg><u>contact@brevonix.com</u></li>
    <li><svg width="14" height="14" viewBox="0 0 14 14"><path d="M7 0a4.5 4.5 0 0 0-4.5 4.5C2.5 8 7 14 7 14s4.5-6 4.5-9.5A4.5 4.5 0 0 0 7 0z" fill="#fff"/><circle cx="7" cy="4.6" r="1.7" fill="#333"/></svg><span>#2868 Lorem ipsum dolor sit amet,<br>consectetur adipiscing elit</span></li>
  </ul>

  <h3 class="abs f-h" style="left:589px;top:1985px">Newsletter</h3>
  <p class="abs f-news-sub" style="left:589px;top:2031px">Sign Up for Our Newsletter &amp; Promotion</p>
  <div class="abs f-input">Enter Your email Id</div>
  <a class="abs btn f-sub">Subscribe</a>

  <div class="abs f-mark"><span class="dot"></span><span class="name">brevonix</span></div>

  <div class="abs footer-bottom"></div>
  <p class="abs copyright">© 2016 /brevonix.com/. All Rights Reserved</p>
  <div class="abs social"><span></span><span></span><span></span><span></span></div>
</footer>

</body>
</html>
```